Business Card Design (NEW FILES)

ATTENTION: New vector files are available. Please update your design to reflect/use the new (better resolution) logo images.

Seeking a unique and professional business card design for a commercial drone photography/videography business. The layout should feature
the logo (attached) and include the following information:
Owen Tarrick
614-502-7738
www.skylarkreelworks.example
NRD Certified Remote Pilot

Owen Tarrick

```html
<!DOCTYPE html>
<html lang="en">
<head>
<meta charset="utf-8">
<title>Skylark Reelworks – Business Card</title>
<link rel="stylesheet" href="https://fonts.googleapis.com/css2?family=Montserrat:wght@400;600;700&family=Open+Sans:wght@400;600&display=swap">
<style>
  :root {
    --stage: #222222;
    --navy: #1b1c4e;
    --orange: #e8894a;
    --gold: #c08a2e;
    --paper: #ffffff;
    --paper-back: #f3f3f3;
  }
  * { box-sizing: border-box; margin: 0; padding: 0; }
  html, body { width: 1200px; height: 780px; overflow: hidden; }
  body {
    background: var(--stage);
    display: flex;
    align-items: center;
    justify-content: center;
    gap: 50px;
    font-family: "Open Sans", Arial, sans-serif;
  }
  .card {
    position: relative;
    width: 525px;
    height: 300px;
    border-radius: 18px;
    overflow: hidden;
    box-shadow: 0 14px 30px rgba(0,0,0,.45);
  }
  .card-front { background: var(--paper); }
  .card-back {
    background: var(--paper-back);
    display: flex;
    align-items: center;
    justify-content: center;
  }
  .wave { position: absolute; inset: 0; width: 100%; height: 100%; }
  .brand {
    display: flex;
    align-items: center;
    gap: 10px;
    font-family: "Montserrat", Arial, sans-serif;
    font-weight: 600;
    color: var(--navy);
    white-space: nowrap;
  }
  .brand-dot {
    width: 14px; height: 14px; border-radius: 50%;
    background: var(--orange);
    flex: none;
  }
  .card-front .brand { position: absolute; left: 28px; top: 26px; font-size: 22px; }
  .card-back .brand { font-size: 40px; gap: 16px; }
  .card-back .brand-dot { width: 26px; height: 26px; }
  .contacts {
    position: absolute;
    left: 30px; top: 84px;
    list-style: none;
    font-size: 13px;
    color: var(--navy);
    line-height: 21px;
  }
  .contacts li { display: flex; align-items: center; gap: 8px; white-space: nowrap; }
  .contacts svg { width: 12px; height: 12px; fill: var(--orange); flex: none; }
  .person {
    position: absolute;
    right: 36px; top: 96px;
    text-align: right;
    font-family: "Montserrat", Arial, sans-serif;
    white-space: nowrap;
  }
  .person-name { font-size: 27px; font-weight: 700; color: var(--navy); letter-spacing: .5px; }
  .person-name .first { color: var(--orange); }
  .person-role { font-family: "Open Sans", Arial, sans-serif; font-size: 14px; color: var(--navy); margin-top: 2px; }
  .gold-tab {
    position: absolute;
    right: 0; top: 150px;
    width: 16px; height: 50px;
    background: var(--gold);
  }
  .credentials {
    position: absolute;
    left: 190px; top: 228px;
    width: 210px;
    color: var(--paper);
    font-size: 14px;
    line-height: 20px;
    text-align: center;
    white-space: nowrap;
  }
</style>
</head>
<body>
  <section class="card card-front">
    <svg class="wave" viewBox="0 0 525 300" aria-hidden="true">
      <path d="M0 300 L0 226 C70 206 150 206 240 204 C340 202 430 225 480 300 Z" fill="var(--navy)"/>
      <path d="M3 168 C12 192 32 206 72 210" fill="none" stroke="var(--orange)" stroke-width="5" stroke-linecap="round"/>
    </svg>
    <div class="brand"><span class="brand-dot"></span>Skylark Reelworks</div>
    <ul class="contacts">
      <li><svg viewBox="0 0 24 24"><path d="M6.6 10.8a15.1 15.1 0 0 0 6.6 6.6l2.2-2.2c.3-.3.7-.4 1-.2 1.1.4 2.3.6 3.6.6.6 0 1 .4 1 1V20c0 .6-.4 1-1 1A17 17 0 0 1 3 4c0-.6.4-1 1-1h3.5c.6 0 1 .4 1 1 0 1.3.2 2.5.6 3.6.1.3 0 .7-.2 1z"/></svg>614-502-7738</li>
      <li><svg viewBox="0 0 24 24"><path d="M12 2a10 10 0 1 0 0 20 10 10 0 0 0 0-20zm6.9 6h-3a15.7 15.7 0 0 0-1.4-3.6A8 8 0 0 1 18.9 8zM12 4c.8 1.2 1.5 2.5 1.9 4h-3.8c.4-1.5 1.1-2.8 1.9-4zM4.3 14a8 8 0 0 1 0-4h3.4a16 16 0 0 0 0 4zm.8 2h3a15.7 15.7 0 0 0 1.4 3.6A8 8 0 0 1 5.1 16zm3-8h-3a8 8 0 0 1 4.4-3.6C8.9 5.5 8.4 6.7 8.1 8zM12 20c-.8-1.2-1.5-2.5-1.9-4h3.8c-.4 1.5-1.1 2.8-1.9 4zm2.3-6H9.7a14.7 14.7 0 0 1 0-4h4.6a14.7 14.7 0 0 1 0 4zm.2 5.6c.6-1.1 1.1-2.3 1.4-3.6h3a8 8 0 0 1-4.4 3.6zm1.8-5.6a16 16 0 0 0 0-4h3.4a8 8 0 0 1 0 4z"/></svg>www.skylarkreelworks.example</li>
      <li><svg viewBox="0 0 24 24"><path d="M20 4H4a2 2 0 0 0-2 2v12a2 2 0 0 0 2 2h16a2 2 0 0 0 2-2V6a2 2 0 0 0-2-2zm0 4-8 5-8-5V6l8 5 8-5z"/></svg>info@skylarkreelworks.example</li>
    </ul>
    <div class="person">
      <div class="person-name"><span class="first">Owen</span> Tarrick</div>
      <div class="person-role">Owner</div>
    </div>
    <div class="gold-tab"></div>
    <p class="credentials">NRD Certified Remote Pilot<br>Fully Insured</p>
  </section>

  <section class="card card-back">
    <div class="brand"><span class="brand-dot"></span>Skylark Reelworks</div>
  </section>
</body>
</html>
```